wealth management firm, professional group, new model

we have a logo that works but we need a card, white background using our colors...clean look

our tag line if can be used in

Steady Counsel for Lasting Wealth

```html
<!DOCTYPE html>
<html lang="en">
<head>
<meta charset="UTF-8">
<title>Corvale Wealth Partners – Business Card</title>
<link href="https://fonts.googleapis.com/css2?family=Montserrat:wght@400;500&display=swap" rel="stylesheet">
<style>
  :root {
    --navy: #13294b;
    --paper: #f2f2f2;
    --backdrop: #262626;
    --band-text: #e4e8ef;
  }
  html, body {
    margin: 0;
    padding: 0;
    overflow: hidden;
  }
  body {
    width: 1200px;
    height: 576px;
    background: var(--backdrop);
    position: relative;
    font-family: "Montserrat", sans-serif;
    color: var(--navy);
  }
  .card {
    position: absolute;
    background: var(--paper);
    border-radius: 9px;
    overflow: hidden;
  }
  .card--front {
    left: 102px;
    top: 139px;
    width: 484px;
    height: 292px;
  }
  .card--back {
    left: 596px;
    top: 138px;
    width: 480px;
    height: 291px;
  }
  .wordmark {
    position: absolute;
    text-align: center;
    font-weight: 400;
    color: var(--navy);
    white-space: nowrap;
  }
  .wordmark__name,
  .wordmark__sub {
    display: block;
    text-transform: uppercase;
  }
  .card--front .wordmark {
    left: 0;
    right: 0;
    top: 127px;
  }
  .card--front .wordmark__name {
    font-size: 40px;
    letter-spacing: 12px;
    margin-right: -12px;
    line-height: 48px;
  }
  .card--front .wordmark__sub {
    font-size: 14px;
    letter-spacing: 2.2px;
    margin-top: 14px;
  }
  .card--back .wordmark {
    left: 17px;
    width: 240px;
    top: 104px;
  }
  .card--back .wordmark__name {
    font-size: 33px;
    letter-spacing: 8px;
    margin-right: -8px;
    line-height: 40px;
  }
  .card--back .wordmark__sub {
    font-size: 12.5px;
    letter-spacing: 1.8px;
    margin-top: 17px;
  }
  .holder {
    position: absolute;
    right: 34px;
    top: 57px;
    text-align: right;
  }
  .holder__name {
    font-size: 21px;
    font-weight: 500;
    line-height: 24px;
    margin: 0;
  }
  .holder__title {
    font-size: 13px;
    font-weight: 400;
    line-height: 16px;
    margin: 0;
  }
  .contact {
    position: absolute;
    right: 32px;
    top: 121px;
    margin: 0;
    padding: 0;
    list-style: none;
    text-align: right;
  }
  .contact__item {
    font-size: 12.5px;
    line-height: 20px;
    display: flex;
    justify-content: flex-end;
    align-items: center;
    gap: 8px;
  }
  .contact__icon {
    width: 11px;
    height: 11px;
    fill: var(--navy);
  }
  .tagline-band {
    position: absolute;
    left: 0;
    right: 0;
    top: 236px;
    height: 39px;
    background: var(--navy);
    color: var(--band-text);
    font-size: 13px;
    letter-spacing: 1px;
    text-transform: uppercase;
    display: flex;
    align-items: center;
    justify-content: center;
  }
</style>
</head>
<body>
  <section class="card card--front" aria-label="Card front">
    <div class="wordmark">
      <span class="wordmark__name">Corvale</span>
      <span class="wordmark__sub">Wealth Partners</span>
    </div>
  </section>

  <section class="card card--back" aria-label="Card back">
    <div class="wordmark">
      <span class="wordmark__name">Corvale</span>
      <span class="wordmark__sub">Wealth Partners</span>
    </div>

    <div class="holder">
      <p class="holder__name">Daniel Mercer</p>
      <p class="holder__title">Managing Director</p>
    </div>

    <ul class="contact">
      <li class="contact__item">555-014-2270
        <svg class="contact__icon" viewBox="0 0 12 12" aria-hidden="true"><path d="M1 4c0-2 2-3 5-3s5 1 5 3v1H8.5V3.6h-5V5H1zM3 6h6l1.5 5h-9z"/><circle cx="6" cy="8.3" r="1.2" fill="#f2f2f2"/></svg>
      </li>
      <li class="contact__item">daniel@example.com
        <svg class="contact__icon" viewBox="0 0 12 12" aria-hidden="true"><path d="M0 2h12v8H0z"/><path d="M0.6 2.6 6 6.8l5.4-4.2" stroke="#f2f2f2" stroke-width="1" fill="none"/></svg>
      </li>
      <li class="contact__item">www.example.com
        <svg class="contact__icon" viewBox="0 0 12 12" aria-hidden="true"><circle cx="6" cy="6" r="5.5"/><path d="M0.5 6h11M6 0.5v11M2 3h8M2 9h8" stroke="#f2f2f2" stroke-width="0.7" fill="none"/><ellipse cx="6" cy="6" rx="2.4" ry="5.5" stroke="#f2f2f2" stroke-width="0.7" fill="none"/></svg>
      </li>
    </ul>

    <div class="tagline-band">Steady Counsel for Lasting Wealth</div>
  </section>
</body>
</html>
```